Website for software company "velora"

We need a website for our software company/startup named "velora". We are developing several products (currently 3 standard-software products) which are all in different sectors, but all our products are available for Laptops/PC/Mobile Phones/Tablets, ... We do also create custom software and support our customers with consulting to optimize their processes.
We already have a Logo which you can find in the attached files.
We are a young team of 4 members (two founders and 2 employees).

To get an idea of our products -> the first one is a planning software for healthcare organizations (eg. BlueHaven, firebrigade, pharmacy), the second one is a booking software for sport clubs and the third one is a competition software for sports hunting. You see very diverse. Include or ignore this info of our products as you like.

The design has to be a bootstrap 4 (or higher) design. We have licenced FontAwesome as iconset. Responsive design should come without saying.

• Starting page, product pages, news section, contact, team, services

```html
<!DOCTYPE html>
<html lang="en">
<head>
<meta charset="utf-8">
<title>velora — Planning Software</title>
<link href="https://fonts.googleapis.com/css2?family=Montserrat:wght@300;400;500;600;700&display=swap" rel="stylesheet">
<style>
:root{
  --orange:#f5842c;
  --orange-deep:#ee6f12;
  --navy:#232a36;
  --ink:#1e2533;
  --text:#3b4150;
  --muted:#6b7180;
  --light:#f3f3f4;
  --white:#ffffff;
  --line:#e2e3e6;
}
*{box-sizing:border-box;margin:0;padding:0}
html,body{width:1200px;height:3904px;overflow:hidden}
body{font-family:"Montserrat",sans-serif;color:var(--text);background:var(--white);position:relative}
section,header,footer{position:relative;width:1200px;overflow:hidden}
.abs{position:absolute}

/* header */
.site-header{height:77px;background:var(--white)}
.brand{left:132px;top:16px;font-size:40px;font-weight:600;color:var(--ink);letter-spacing:1px;line-height:44px;text-transform:uppercase}
.nav{top:0;left:0}
.nav a{position:absolute;top:31px;font-size:12px;font-weight:600;color:var(--ink);text-decoration:none;letter-spacing:.3px}
.nav a.active::after{content:"";position:absolute;left:0;right:0;top:26px;height:2px;background:var(--orange)}
.btn-dark{left:959px;top:21px;width:124px;height:37px;border-radius:19px;background:var(--navy);color:var(--white);font-size:12px;font-weight:600;display:flex;align-items:center;justify-content:center;letter-spacing:.4px}

/* hero */
.hero{height:473px;background:linear-gradient(90deg,#1b2126 0%,#2a3034 38%,#5a4a3c 62%,#8a5a36 80%,#4a3a30 100%)}
.hero-photo{left:0;top:0;width:1200px;height:473px;background:radial-gradient(ellipse at 72% 40%,rgba(190,110,60,.55),rgba(0,0,0,0) 45%),linear-gradient(180deg,rgba(0,0,0,.1),rgba(0,0,0,.35))}
.hero-kicker{left:110px;top:238px;font-size:27px;line-height:32px;font-weight:400;color:var(--white)}
.hero-title{left:110px;top:270px;font-size:37px;line-height:42px;font-weight:700;color:var(--white)}
.hero-text{left:112px;top:320px;width:420px;font-size:15px;line-height:22px;color:#e7e7e7}

/* about */
.about{height:491px}
.about-media{left:83px;top:56px;width:493px;height:394px;border-radius:8px;background:radial-gradient(ellipse at 50% 45%,#e9ecf3 0%,#f4f5f8 55%,#ffffff 80%)}
.eyebrow{font-size:15px;color:var(--orange);font-weight:400;letter-spacing:.3px}
.about .eyebrow{left:609px;top:110px}
.h-split{font-size:34px;line-height:38px;color:var(--ink);font-weight:400}
.h-split b{font-weight:700}
.about .h-split{left:609px;top:133px}
.about p{position:absolute;left:610px;width:470px;font-size:15px;line-height:23px;color:var(--text)}

/* features */
.features{height:538px;background:linear-gradient(180deg,var(--light) 0%,var(--light) 60%,#f8f8f8 100%)}
.center-title{left:0;width:1200px;text-align:center;font-size:26px;line-height:33px;color:var(--ink);font-weight:400}
.center-title b{font-weight:700}
.rule{height:3px;width:74px;background:var(--orange);left:563px}
.card{top:214px;width:258px;height:197px;border-radius:8px;padding:30px 35px 0;box-shadow:0 6px 18px rgba(0,0,0,.06)}
.card h3{font-size:17px;font-weight:700;margin-top:18px;letter-spacing:.3px}
.card p{font-size:12.5px;line-height:18px;margin-top:10px}
.card svg{display:block}
.card-light{left:183px;background:var(--white);color:var(--ink)}
.card-light p{color:var(--text)}
.card-orange{left:467px;background:var(--orange);color:var(--white)}
.card-dark{left:751px;background:var(--navy);color:var(--white)}
.card-dark h3{color:var(--white)}

/* checklists */
.split{height:451px}
.split2{height:549px}
.checklist{list-style:none}
.checklist li{position:absolute;padding-left:43px;font-size:13.5px;line-height:20px;font-weight:600;color:var(--ink);width:470px}
.checklist li svg{position:absolute;left:0;top:1px}
.media-dash{left:633px;top:80px;width:453px;height:328px;background:linear-gradient(180deg,#d9dadd 0 18px,#e9eaed 18px,#f2f3f5 100%);border-radius:2px}
.media-tablet{left:136px;top:83px;width:455px;height:372px;border-radius:14px;background:linear-gradient(135deg,#1f2329 0%,#3a3f48 45%,#c9cdd6 80%,#eef0f5 100%)}

/* services */
.services{height:547px;background:var(--light)}
.services-title{left:0;width:1200px;text-align:center;top:66px;font-size:34px;line-height:40px;color:var(--ink);font-weight:400}
.services-title b{font-weight:700}
.svc{width:431px;height:131px;background:var(--white);box-shadow:0 4px 14px rgba(0,0,0,.05)}
.svc .ico{position:absolute;left:22px;top:26px;width:68px;height:68px;border-radius:50%;background:var(--navy);display:flex;align-items:center;justify-content:center}
.svc h4{position:absolute;left:113px;top:35px;font-size:13.5px;font-weight:700;color:var(--ink);letter-spacing:.3px}
.svc p{position:absolute;left:113px;top:60px;width:290px;font-size:12px;line-height:17px;color:var(--text)}

/* contact */
.contact{height:459px}
.contact-bg{left:0;top:0;width:1200px;height:459px;background:linear-gradient(135deg,var(--orange-deep) 0%,var(--orange) 50%,#f06d18 100%)}
.contact-title{left:0;width:1200px;text-align:center;top:72px;font-size:30px;line-height:36px;color:var(--white);font-weight:300}
.contact-title b{font-weight:700}
.contact .rule{background:var(--white);left:563px;top:113px;height:3px;width:74px}
.field{background:var(--white);font-size:12.5px;color:var(--ink);padding:0 16px;display:flex;align-items:center}
.field.area{align-items:flex-start;padding-top:18px}
.btn-send{left:542px;top:347px;width:150px;height:41px;border-radius:21px;background:var(--navy);color:var(--white);font-size:12.5px;font-weight:700;display:flex;align-items:center;justify-content:center;letter-spacing:.4px}

/* footer */
.site-footer{height:319px;background:var(--white)}
.footer-brand{left:164px;top:76px;font-size:40px;line-height:44px;font-weight:600;color:var(--ink);text-transform:uppercase;letter-spacing:1px}
.footer-about{left:164px;top:135px;width:240px;font-size:11px;line-height:15px;color:var(--muted)}
.vline{width:1px;background:var(--line);top:0;height:255px}
.vline::before{content:"";position:absolute;left:0;top:52px;width:3px;height:26px;background:var(--orange)}
.fcol h5{font-size:13px;font-weight:700;color:var(--ink);letter-spacing:.3px}
.fcol a{display:block;font-size:12.5px;color:var(--text);text-decoration:none;margin-top:14px}
.social{display:flex;gap:6px;margin-top:14px}
.social span{width:29px;height:29px;border-radius:50%;background:var(--navy)}
.social span:first-child{background:var(--orange)}
.footer-bottom{left:0;top:286px;width:1200px;border-top:1px solid var(--line);text-align:center;font-size:11px;color:var(--muted);padding-top:10px}
</style>
</head>
<body>

<header class="site-header">
  <div class="abs brand">velora</div>
  <nav class="abs nav">
    <a class="active" style="left:421px">PRODUCT</a>
    <a style="left:544px">SERVICES</a>
    <a style="left:667px">NEWS</a>
    <a style="left:767px">TEAM</a>
    <a style="left:862px">ABOUT</a>
  </nav>
  <div class="abs btn-dark">CONTACT</div>
</header>

<section class="hero">
  <div class="abs hero-photo" role="img" aria-label="Photo of a man working on a laptop in a dim office"></div>
  <div class="abs hero-kicker">SED UT PERSPICIATIS</div>
  <div class="abs hero-title">PLANNING SOFTWARE</div>
  <p class="abs hero-text">Lorem ipsum dolor sit amet, consectetur adipiscing elit, sed do eiusmod tempor incididunt.</p>
</section>

<section class="about">
  <div class="abs about-media" role="img" aria-label="Desktop monitor showing the planning software dashboard"></div>
  <div class="abs eyebrow">PRODUCT&nbsp; TITLE</div>
  <h2 class="abs h-split">ABOUT PLANNING<br><b>SOFTWARE</b></h2>
  <p style="top:230px">Lorem ipsum dolor sit amet, consectetur adipiscing elit, sed do eiusmod tempor incididunt ut laborLorem ipsum dolor sit amet, consectetur adipiscing elit, sed do eiusmoLorem ipsum dolor sit amet, consectetur adipiscing elit, sed do</p>
  <p style="top:338px">Aiusmod tempor incididunt ut laborLorem ipsum dolor sit amet, consectetur adipiscing elit, sed do eiusmo</p>
</section>

<section class="features">
  <h2 class="abs center-title" style="top:77px">SED UT PERSPICIATIS UNDE OMNIS ISTE<br><b>NATUS ERROR SIT VOLUPTAT</b></h2>
  <div class="abs rule" style="top:156px"></div>

  <div class="abs card card-light">
    <svg width="40" height="40" viewBox="0 0 40 40" fill="none" stroke="#f5842c" stroke-width="1.8"><circle cx="20" cy="20" r="17"/><circle cx="20" cy="20" r="11"/><circle cx="20" cy="20" r="5"/></svg>
    <h3>VOLUPTATEM</h3>
    <p>Lorem ipsum dolor sit amet, consectetur adipiscing elit, sed do eiusmod tempo</p>
  </div>
  <div class="abs card card-orange">
    <svg width="44" height="40" viewBox="0 0 44 40" fill="none" stroke="#fff" stroke-width="1.8"><circle cx="22" cy="12" r="8"/><circle cx="22" cy="12" r="3"/><path d="M4 30c6-4 12-4 18-1h10c2 0 2 3 0 3H20M4 36c10 2 20 1 34-8"/></svg>
    <h3>SUPPORT</h3>
    <p>Lorem ipsum dolor sit amet, consectetur adipiscing elit, sed do eiusmod tempo</p>
  </div>
  <div class="abs card card-dark">
    <svg width="42" height="40" viewBox="0 0 42 40" fill="none" stroke="#f5842c" stroke-width="1.8"><rect x="2" y="3" width="38" height="26" rx="2"/><path d="M17 11l-5 5 5 5M25 11l5 5-5 5M21 29v7M13 37h16"/></svg>
    <h3>DEVELOP</h3>
    <p>Lorem ipsum dolor sit amet, consectetur adipiscing elit, sed do eiusmod tempo</p>
  </div>
</section>

<section class="split">
  <h2 class="abs h-split" style="left:145px;top:105px;font-size:27px;line-height:33px">SED UT PERSPICIATIS UNDE<br><b>NATUS ERROR SIT</b></h2>
  <ul class="checklist">
    <li style="left:145px;top:200px"><svg width="22" height="22" viewBox="0 0 22 22"><circle cx="11" cy="11" r="10" fill="#f5842c"/><path d="M6.5 11.5l3 3 6-6.5" stroke="#fff" stroke-width="2.2" fill="none"/></svg>Lorem ipsum dolor sit amet, consectetur adipiscing elit, sed do eiusmod tempor incididunt ut labor</li>
    <li style="left:145px;top:268px"><svg width="22" height="22" viewBox="0 0 22 22"><circle cx="11" cy="11" r="10" fill="#f5842c"/><path d="M6.5 11.5l3 3 6-6.5" stroke="#fff" stroke-width="2.2" fill="none"/></svg>Lorem ipsum dolor sit amet, consectetur adipiscing elit, sed do eiusmoLorem ipsum dolor sit amet</li>
    <li style="left:145px;top:336px"><svg width="22" height="22" viewBox="0 0 22 22"><circle cx="11" cy="11" r="10" fill="#f5842c"/><path d="M6.5 11.5l3 3 6-6.5" stroke="#fff" stroke-width="2.2" fill="none"/></svg>Aiusmod tempor incididunt ut laborLorem ipsum dolor sit amet, consectetur adipiscing elit</li>
  </ul>
  <div class="abs media-dash" role="img" aria-label="Analytics dashboard with user, order, download and percentage widgets"></div>
</section>

<section class="split2">
  <div class="abs media-tablet" role="img" aria-label="Tablet and phone showing the planning interface"></div>
  <h2 class="abs h-split" style="left:653px;top:102px;font-size:27px;line-height:33px">EASY PLANNING INTERFACE<br><b>NATUS ERROR SIT</b></h2>
  <ul class="checklist">
    <li style="left:653px;top:202px"><svg width="22" height="22" viewBox="0 0 22 22"><circle cx="11" cy="11" r="10" fill="#232a36"/><path d="M6.5 11.5l3 3 6-6.5" stroke="#fff" stroke-width="2.2" fill="none"/></svg>Lorem ipsum dolor sit amet, consectetur adipiscing elit, sed do eiusmod tempor incididunt ut labor</li>
    <li style="left:653px;top:270px"><svg width="22" height="22" viewBox="0 0 22 22"><circle cx="11" cy="11" r="10" fill="#232a36"/><path d="M6.5 11.5l3 3 6-6.5" stroke="#fff" stroke-width="2.2" fill="none"/></svg>Lorem ipsum dolor sit amet, consectetur adipiscing elit, sed do eiusmoLorem ipsum dolor sit amet</li>
    <li style="left:653px;top:338px"><svg width="22" height="22" viewBox="0 0 22 22"><circle cx="11" cy="11" r="10" fill="#232a36"/><path d="M6.5 11.5l3 3 6-6.5" stroke="#fff" stroke-width="2.2" fill="none"/></svg>Aiusmod tempor incididunt ut laborLorem ipsum dolor sit amet, consectetur adipiscing elit</li>
  </ul>
</section>

<section class="services">
  <h2 class="abs services-title">OUR <b>SERVICES</b></h2>
  <div class="abs rule" style="top:127px;left:563px"></div>

  <div class="abs svc" style="left:152px;top:152px">
    <div class="ico"><svg width="34" height="30" viewBox="0 0 34 30" fill="none" stroke="#fff" stroke-width="1.5"><rect x="2" y="2" width="30" height="20"/><path d="M8 16l5-5 4 3 7-7M12 28h10M17 22v6"/></svg></div>
    <h4>LOREM IPSUM DOLOR</h4>
    <p>Neque porro quisquam est, qui dolorem ipsum quia dolor sit amet, consectetur adipisci</p>
  </div>
  <div class="abs svc" style="left:598px;top:152px">
    <div class="ico"><svg width="32" height="30" viewBox="0 0 32 30" fill="none" stroke="#fff" stroke-width="1.5"><rect x="2" y="5" width="28" height="23"/><path d="M2 11h28M9 2v6M23 2v6M11 19l4 4 7-7"/></svg></div>
    <h4>LOREM IPSUM DOLOR</h4>
    <p>Neque porro quisquam est, qui dolorem ipsum quia dolor sit amet, consectetur adipisci</p>
  </div>
  <div class="abs svc" style="left:152px;top:298px">
    <div class="ico"><svg width="32" height="32" viewBox="0 0 32 32" fill="none" stroke="#fff" stroke-width="1.5"><rect x="3" y="2" width="20" height="26"/><path d="M7 8h12M7 13h12M7 18h7"/><circle cx="23" cy="23" r="6"/><path d="M20 23l2 2 4-4"/></svg></div>
    <h4>LOREM IPSUM DOLOR</h4>
    <p>Neque porro quisquam est, qui dolorem ipsum quia dolor sit amet, consectetur adipisci</p>
  </div>
  <div class="abs svc" style="left:598px;top:298px">
    <div class="ico"><svg width="34" height="32" viewBox="0 0 34 32" fill="none" stroke="#fff" stroke-width="1.5"><path d="M10 3h21v17h-4"/><path d="M3 9h22v16H11l-6 5v-5H3z"/></svg></div>
    <h4>LOREM IPSUM DOLOR</h4>
    <p>Neque porro quisquam est, qui dolorem ipsum quia dolor sit amet, consectetur adipisci</p>
  </div>
</section>

<section class="contact">
  <div class="abs contact-bg" role="img" aria-label="Orange tinted background of an office scene"></div>
  <h2 class="abs contact-title">CONTACT <b>VELORA</b></h2>
  <div class="abs rule"></div>
  <div class="abs field" style="left:238px;top:145px;width:374px;height:52px">Name*</div>
  <div class="abs field" style="left:238px;top:206px;width:374px;height:52px">Email address*</div>
  <div class="abs field" style="left:238px;top:267px;width:374px;height:53px">Phone*</div>
  <div class="abs field area" style="left:621px;top:145px;width:374px;height:175px">Message</div>
  <div class="abs btn-send">CONTACT US</div>
</section>

<footer class="site-footer">
  <div class="abs footer-brand">velora</div>
  <p class="abs footer-about">Lorem ipsum dolor sit amet, consectetur adipiscing elit, sed do eiusmod tempor incididunt ut labore et dolore</p>
  <div class="abs vline" style="left:447px"></div>
  <div class="abs vline" style="left:679px"></div>
  <div class="abs vline" style="left:903px"></div>
  <div class="abs fcol" style="left:489px;top:58px">
    <h5>NAVIGATION</h5>
    <a>About Us</a><a>Products</a><a>Services</a><a>Contact Us</a>
  </div>
  <div class="abs fcol" style="left:726px;top:58px">
    <h5>RESOURCES</h5>
    <a>News</a><a>Team</a><a>Privacy Policy</a>
  </div>
  <div class="abs fcol" style="left:933px;top:58px">
    <h5>FOLLOW US</h5>
    <div class="social"><span></span><span></span><span></span><span></span></div>
  </div>
  <div class="abs footer-bottom">© 2022 velora &nbsp;| All Rights Reserved</div>
</footer>

</body>
</html>
```